Pizza Box 10" x 10" - color: White

Custom design, utilizing CrustVarko Logo and include the following information on the Pizza Box:

1. Custom Crafted Pizza with Quality Ingredients.
2. [....Get Your GAME ON] to be placed on the front flap and seen when the
box is opened.
3. You"ll miss 100% of the Pizza you don't eat.

4. Visit www.lumacartonworks.com for additional design resource information. Go to site and then click on ORDERING to access.

5. The 10" x 10" Pizza Box is to be in the color WHITE.
6. Use colors Black and Red. no generic images. no food pics. I am looking for a clean and cool design.

Target Market(s)

Age 16 - 36 years

Industry/Entity Type

American Restaurant

Font styles to use
Sans Serif

Colors
ec1f27
000000
ffffff

Requirements
Must have
• Color Red and Black.
• Logo on Top and all sides of the Pizza Box.
Nice to have
• A Creative design that does not look generic.
Should not have
• No food images.

```html
<!DOCTYPE html>
<html lang="en">
<head>
<meta charset="utf-8">
<title>CrustVarko Pizza Box Lid</title>
<link rel="stylesheet" href="https://fonts.googleapis.com/css2?family=Roboto+Condensed:ital,wght@1,400;1,700&family=Ubuntu:wght@700&display=swap">
<style>
  :root {
    --brand-red: #ec1f27;
    --brand-black: #1c1c1c;
    --board-white: #ecebe9;
    --board-edge: #dcdbd9;
    --stage: #f2f2f2;
    --ink-soft: #3a3a3a;
  }
  * { margin: 0; padding: 0; box-sizing: border-box; }
  html, body {
    width: 1200px;
    height: 1000px;
    overflow: hidden;
    background: var(--stage);
  }
  .canvas {
    position: relative;
    width: 1200px;
    height: 1000px;
  }
  .box-lid {
    position: absolute;
    left: 150px;
    top: 110px;
    width: 900px;
    height: 620px;
    background: var(--board-white);
    border: 1px solid var(--board-edge);
  }
  .box-front {
    position: absolute;
    left: 150px;
    top: 740px;
    width: 900px;
    height: 140px;
    background: var(--board-white);
    border: 1px solid var(--board-edge);
    display: flex;
    align-items: center;
    justify-content: center;
  }
  .chef-figure {
    position: absolute;
    left: 355px;
    top: 40px;
    width: 190px;
    height: 400px;
    background: linear-gradient(180deg, #dedddb 0%, #e6e5e3 100%);
    border-radius: 6px;
  }
  .brand-lockup {
    position: absolute;
    left: 0;
    width: 100%;
    display: flex;
    align-items: center;
    justify-content: center;
    gap: 18px;
  }
  .brand-lockup--lid { top: 200px; }
  .brand-mark {
    width: 78px;
    height: 78px;
    border-radius: 50%;
    border: 6px solid var(--brand-red);
    flex: none;
  }
  .brand-name {
    font-family: "Ubuntu", sans-serif;
    font-weight: 700;
    font-size: 72px;
    letter-spacing: 1px;
    color: var(--brand-black);
    line-height: 1;
  }
  .brand-lockup--front .brand-mark { width: 68px; height: 68px; border-width: 5px; }
  .brand-lockup--front .brand-name { font-size: 62px; }
  .brand-lockup--front { position: static; }
  .taglines {
    position: absolute;
    left: 0;
    top: 470px;
    width: 100%;
    text-align: center;
    font-family: "Roboto Condensed", sans-serif;
    font-style: italic;
    font-size: 22px;
    line-height: 1.3;
    color: var(--ink-soft);
  }
  .taglines .accent { color: var(--brand-red); font-weight: 700; }
</style>
</head>
<body>
  <main class="canvas">
    <section class="box-lid">
      <div class="chef-figure" role="img" aria-label="Line illustration of a chef with toque, moustache and buttoned jacket"></div>
      <div class="brand-lockup brand-lockup--lid">
        <span class="brand-mark"></span>
        <span class="brand-name">CrustVarko</span>
      </div>
      <div class="taglines">
        <p>Custom Crafted Pizza with <span class="accent">Quality</span> Ingredients</p>
        <p>You"ll miss <span class="accent">100%</span> of the <span class="accent">Pizza</span> you don't eat</p>
      </div>
    </section>
    <section class="box-front">
      <div class="brand-lockup brand-lockup--front">
        <span class="brand-mark"></span>
        <span class="brand-name">CrustVarko</span>
      </div>
    </section>
  </main>
</body>
</html>
```